Boutique custom software development company needs new business card

Our nearly 20 year old custom software development company would like to better include the fact that we are now providing Bitcoin services. These new services are B2B include education (how to acquire and securely hold Bitcoin) and integrating Bitcoin payments into existing ecommerce sites or other existing systems. Please keep the card clean and simple. Attached is our current design and some other files. vextorial.com

Target Market(s)

businesses owners interested in long term relationship

Industry/Entity Type

Custom software development and Bitcoin

Contact Information for Business Card

Dale Parker, dale@vextorial.com, vextorial.com, (888) 555-VXTRL

Font styles to use
Other font styles liked:
• monospace

Requirements
Must have
• double-sided
Nice to have
• clean and simple
Should not have
• physical address

```html
<!DOCTYPE html>
<html lang="en">
<head>
<meta charset="utf-8">
<title>Vextorial Business Card</title>
<link rel="stylesheet" href="https://fonts.googleapis.com/css2?family=Lato:wght@400;900&family=Roboto+Mono:wght@400;500&display=swap">
<style>
  :root {
    --page-bg: #111214;
    --card-bg: #0a1534;
    --brand-blue: #3d70c2;
    --brand-orange: #ea7b29;
  }
  * { margin: 0; padding: 0; box-sizing: border-box; }
  html, body {
    width: 1200px; height: 848px; overflow: hidden;
    background: var(--page-bg);
  }
  .canvas { position: relative; width: 1200px; height: 848px; }
  .card {
    position: absolute; left: 281px; width: 615px; height: 334px;
    background: var(--card-bg);
  }
  .card--front { top: 68px; }
  .card--back { top: 445px; }

  .brand {
    position: absolute; left: 0; right: 0; top: 122px;
    text-align: center;
  }
  .brand__name {
    font-family: 'Lato', sans-serif; font-weight: 900;
    font-size: 58px; line-height: 1; letter-spacing: 1px;
    color: var(--brand-blue);
  }
  .brand__tagline {
    margin-top: 6px;
    font-family: 'Lato', sans-serif; font-weight: 400;
    font-size: 20px; letter-spacing: -0.6px; line-height: 1.2;
    color: var(--brand-blue);
  }
  .brand__services {
    margin-top: 8px;
    font-family: 'Roboto Mono', monospace; font-weight: 400;
    font-size: 12px; letter-spacing: 0.5px; line-height: 1.2;
    color: var(--brand-orange);
  }

  .identity {
    position: absolute; left: 187px; top: 123px;
    width: 94px; height: 90px;
    display: flex; align-items: center; justify-content: center;
    font-family: 'Roboto Mono', monospace; font-weight: 500;
    font-size: 14px; color: var(--brand-blue);
  }
  .divider {
    position: absolute; left: 307px; top: 121px;
    width: 1.5px; height: 93px; background: var(--brand-orange);
  }
  .contact { position: absolute; left: 333px; top: 118px; }
  .contact__name {
    font-family: 'Roboto Mono', monospace; font-weight: 500;
    font-size: 24px; letter-spacing: 1.5px; line-height: 1;
    color: var(--brand-blue); margin-bottom: 12px;
  }
  .contact__list { list-style: none; }
  .contact__item {
    display: flex; align-items: center; gap: 6px;
    font-family: 'Roboto Mono', monospace; font-weight: 400;
    font-size: 14px; line-height: 18.6px;
    color: var(--brand-orange);
  }
  .contact__icon { width: 12px; height: 12px; fill: var(--brand-blue); flex: none; }
</style>
</head>
<body>
<main class="canvas">
  <section class="card card--front">
    <div class="brand">
      <div class="brand__name">VEXTORIAL</div>
      <div class="brand__tagline">custom applications &amp; bitcoin services</div>
      <div class="brand__services">bitcoin education · payment integration</div>
    </div>
  </section>

  <section class="card card--back">
    <div class="identity">vextorial</div>
    <div class="divider"></div>
    <div class="contact">
      <div class="contact__name">Dale Parker</div>
      <ul class="contact__list">
        <li class="contact__item">
          <svg class="contact__icon" viewBox="0 0 24 24"><path d="M6.6 10.8a15.1 15.1 0 0 0 6.6 6.6l2.2-2.2c.3-.3.7-.4 1-.2 1.1.4 2.3.6 3.6.6.6 0 1 .4 1 1V20c0 .6-.4 1-1 1A17 17 0 0 1 3 4c0-.6.4-1 1-1h3.5c.6 0 1 .4 1 1 0 1.3.2 2.5.6 3.6.1.3 0 .7-.2 1z"/></svg>
          (888) 555-VXTRL
        </li>
        <li class="contact__item">
          <svg class="contact__icon" viewBox="0 0 24 24"><path d="M2 5h20v14H2z M2 5l10 8 10-8" fill="var(--brand-blue)" stroke="var(--card-bg)" stroke-width="1.5"/></svg>
          dale@vextorial.com
        </li>
        <li class="contact__item">
          <svg class="contact__icon" viewBox="0 0 24 24"><circle cx="12" cy="12" r="10" fill="none" stroke="var(--brand-blue)" stroke-width="2"/><path d="M2 12h20M12 2c3 3 3 17 0 20M12 2c-3 3-3 17 0 20" fill="none" stroke="var(--brand-blue)" stroke-width="1.6"/></svg>
          vextorial.com
        </li>
      </ul>
    </div>
  </section>
</main>
</body>
</html>
```